Non fiction leadership Book Cover design needed for “Stay Bold: Build On Lasting Discipline”

I need a front cover design for a new book 6 X 9 traditional non-fiction book.

Title: "Stay BOLD - Build On Lasting Discipline"

The subtitle is not finalized- so use 2 lines of smaller dummy text

My brand guide is attached (please use the tan color sparingly)

I'd like to see BOLD look like it is in motion and "flying" across the page

Need CREATIVE designs and options

Do not want my picture on the front cover - I do want it on the back cover.

On the front cover I’d like to see creative use of font to create movement on “BOLD”

Target Market(s)

Business leaders

Industry/Entity Type

Aviation

Font styles to use
Other font styles liked:
• See style guide- can add additional font (modern script or san serif)

Colors
0054AA
0677BA
7BADD7
CADEEF
E8F1F8
EB3D1F
EC4F4E
F09395
F8D3D4
FCEDEE

Requirements
Must have
• Creative font use, using perspective to create movement/motion on BOLD
Should not have
• My picture on the front cover- my picture should be on the back cover

```html
<!DOCTYPE html>
<html lang="en">
<head>
<meta charset="utf-8">
<title>Stay Bold: Build On Lasting Discipline — Cover</title>
<link rel="stylesheet" href="https://fonts.googleapis.com/css2?family=Bebas+Neue&family=Montserrat:wght@400&display=swap">
<style>
  :root {
    --backdrop: #acaaab;
    --cover-black: #151515;
    --cover-charcoal: #2b2b2b;
    --title-white: #ffffff;
    --navy: #0054aa;
    --blue: #0677ba;
    --sky: #7badd7;
    --mist: #cadeef;
    --ice: #e8f1f8;
    --red: #eb3d1f;
    --coral: #ec4f4e;
    --blush: #f09395;
    --tan: #c98840;
  }
  * { margin: 0; padding: 0; box-sizing: border-box; }
  html, body {
    width: 1200px; height: 1200px; overflow: hidden;
    background: var(--backdrop);
  }
  .cover {
    position: absolute;
    left: 227px; top: 40px;
    width: 746px; height: 1119px;
    background: linear-gradient(160deg, var(--cover-black) 55%, var(--cover-charcoal) 100%);
    overflow: hidden;
  }
  .speed-lines {
    position: absolute; left: 0; top: 70px;
    width: 746px; height: 160px;
  }
  .title {
    font-family: "Bebas Neue", sans-serif;
    font-weight: 400;
  }
  .title-lead {
    position: absolute; left: 0; right: 0; top: 40px;
    text-align: center;
    font-size: 184px;
    line-height: 1;
    color: var(--title-white);
    text-shadow: 6px 8px 14px rgba(0,0,0,0.85);
    white-space: nowrap;
  }
  .title-bold {
    display: inline-block;
    color: var(--coral);
    transform: perspective(420px) rotateY(-16deg) skewX(-12deg);
    transform-origin: left center;
    text-shadow:
      -10px 0 0 rgba(236,79,78,0.45),
      -22px 0 0 rgba(240,147,149,0.28),
      -36px 0 0 rgba(248,211,212,0.14),
      6px 8px 14px rgba(0,0,0,0.85);
  }
  .title-rest {
    position: absolute; left: 0; right: 0; top: 222px;
    text-align: center;
    font-size: 128px;
    line-height: 0.84;
    background: linear-gradient(180deg, var(--ice) 0%, var(--sky) 45%, var(--blue) 100%);
    background-size: 100% 0.84em;
    -webkit-background-clip: text;
    background-clip: text;
    color: transparent;
  }
  .subtitle {
    position: absolute; left: 0; right: 0; top: 566px;
    text-align: center;
    font-family: "Montserrat", sans-serif;
    font-size: 27px;
    line-height: 1.42;
    color: var(--title-white);
  }
  .author {
    position: absolute; top: 672px; left: 268px;
    display: flex; align-items: center; gap: 10px;
    font-family: "Bebas Neue", sans-serif;
    font-size: 46px;
    letter-spacing: 1px;
    color: var(--coral);
  }
  .author-mark {
    width: 14px; height: 14px;
    background: var(--tan);
  }
  .flight-art {
    position: absolute; left: 0; right: 0; bottom: 0;
    height: 380px;
    background:
      radial-gradient(ellipse at 75% 18%, rgba(235,61,31,0.28) 0%, rgba(235,61,31,0) 40%),
      radial-gradient(ellipse at 40% 65%, rgba(202,222,239,0.18) 0%, rgba(202,222,239,0) 55%),
      linear-gradient(180deg, rgba(28,28,28,0) 0%, #222 30%, #2c2c2c 100%);
  }
</style>
</head>
<body>
  <main class="cover">
    <svg class="speed-lines" viewBox="0 0 746 160" aria-hidden="true">
      <defs>
        <linearGradient id="trail" x1="0" x2="1">
          <stop offset="0" stop-color="#eb3d1f" stop-opacity="0"/>
          <stop offset="1" stop-color="#ec4f4e" stop-opacity="0.9"/>
        </linearGradient>
      </defs>
      <g stroke="url(#trail)" stroke-linecap="round">
        <line x1="20" y1="32" x2="360" y2="32" stroke-width="4"/>
        <line x1="60" y1="74" x2="350" y2="74" stroke-width="6"/>
        <line x1="10" y1="112" x2="340" y2="112" stroke-width="3"/>
        <line x1="90" y1="142" x2="355" y2="142" stroke-width="4"/>
      </g>
    </svg>
    <h1 class="title">
      <span class="title-lead">STAY <span class="title-bold">BOLD</span></span>
      <span class="title-rest">BUILD ON<br>LASTING<br>DISCIPLINE</span>
    </h1>
    <p class="subtitle">A BEGINNER’S GUIDE TO EFFECTIVE<br>LEADERSHIP AND MANAGEMENT</p>
    <div class="author"><span class="author-name">HELENA MARSH</span><span class="author-mark"></span></div>
    <div class="flight-art" role="img" aria-label="Illustration of a formation of white paper planes led by a red paper plane, with scattered sparkles on a dark background"></div>
  </main>
</body>
</html>
```